LM-Steuerberatung WordPress Site fully implemented (tax advisor)

Hello!
I need a little Wordpress Site for my newly founded Tax-Advisor Company.
I am a one-man Office advising in the area of Crypto-Currency.
PLEASE only provide a Design, if you can also Implement a WP-Site afterwards on an existing Webspace.

Please find the Content and Website-Description in the attached Document

Language for the Website is German (for now)

Target Market(s)

Tax-Advisory (specialized in Crypto Currency)

Coding

Coded - Design and coding required

Number of Pages Required

5+ page

Font styles to use
Sans Serif

Requirements
Must have
• Wordpress Implementation afterwards - Details according to attached Project Information Document

```html
<!DOCTYPE html>
<html lang="de">
<head>
<meta charset="utf-8">
<title>LM-Steuerberatung</title>
<link href="https://fonts.googleapis.com/css2?family=Montserrat:wght@600;700&family=Roboto:wght@400;500;700&display=swap" rel="stylesheet">
<style>
  :root {
    --navy: #1b2a44;
    --navy-bright: #1f3a6e;
    --ring: #34496f;
    --grey-text: #8d8d8d;
    --text: #1e1e1e;
    --line: #e3e4e7;
    --bg: #ffffff;
  }
  * { margin: 0; padding: 0; box-sizing: border-box; }
  html, body { width: 1200px; height: 758px; overflow: hidden; background: var(--bg); }
  body { font-family: "Roboto", Arial, sans-serif; color: var(--text); }
  .page {
    position: relative; width: 1200px; height: 758px; overflow: hidden;
    background: radial-gradient(ellipse at 30% 45%, #ffffff 0%, #ffffff 45%, #f1f2f4 100%);
  }
  .shapes { position: absolute; inset: 0; }
  .site-header { position: absolute; top: 0; left: 0; width: 100%; height: 120px; }
  .brand {
    position: absolute; left: 111px; top: 44px;
    display: flex; align-items: center; gap: 12px;
    font-family: "Montserrat", sans-serif; font-weight: 600; font-size: 17px;
    letter-spacing: 1.5px; color: var(--navy);
  }
  .brand-square { width: 30px; height: 30px; background: var(--navy); }
  .main-nav {
    position: absolute; top: 51px; left: 467px;
    display: flex; align-items: center;
    font-size: 16px; font-weight: 400; color: var(--text);
  }
  .main-nav a { color: inherit; text-decoration: none; margin-right: 31px; white-space: nowrap; }
  .main-nav a.active { color: var(--navy); font-weight: 500; }
  .has-sub { display: inline-flex; align-items: center; gap: 13px; }
  .lang { display: inline-flex; align-items: center; gap: 7px; font-weight: 500; margin-left: 2px; }
  .hero-text { position: absolute; left: 108px; top: 242px; width: 470px; }
  .hero-kicker {
    font-family: "Montserrat", sans-serif; font-weight: 700; font-size: 23px;
    color: var(--grey-text); letter-spacing: 0.3px;
  }
  .hero-title {
    font-family: "Montserrat", sans-serif; font-weight: 700; font-size: 37px;
    color: var(--navy-bright); margin-top: 8px; letter-spacing: 0.2px;
  }
  .hero-lead { font-weight: 500; font-size: 16px; line-height: 26px; margin-top: 10px; color: #262626; }
  .hero-body { font-size: 16px; line-height: 31px; margin-top: 10px; color: #262626; }
  .btn-primary {
    display: inline-block; margin-top: 25px; background: var(--navy); color: #fff;
    font-size: 13.5px; font-weight: 500; padding: 17px 23px; border-radius: 3px;
    text-decoration: none; letter-spacing: 0.1px;
  }
  .slider-controls { position: absolute; left: 106px; top: 603px; display: flex; gap: 11px; }
  .slider-btn {
    width: 63px; height: 56px; border: 1px solid var(--navy); border-radius: 3px;
    background: #fff; display: flex; align-items: center; justify-content: center;
  }
</style>
</head>
<body>
<div class="page">
  <svg class="shapes" viewBox="0 0 1200 758" width="1200" height="758">
    <defs>
      <clipPath id="photo-clip">
        <polygon points="870,182 1094,306 1094,552 870,676 646,552 646,306" stroke-linejoin="round"/>
      </clipPath>
      <linearGradient id="photo-tone" x1="0" y1="0" x2="1" y2="1">
        <stop offset="0" stop-color="#b9c9a8"/>
        <stop offset="0.45" stop-color="#6f8fb3"/>
        <stop offset="1" stop-color="#dfe3e8"/>
      </linearGradient>
    </defs>
    <polygon class="corner" points="0,0 72,0 0,145" fill="var(--navy)"/>
    <polygon class="corner" points="1200,626 1200,758 1071,758" fill="var(--navy)"/>
    <polygon points="1030,155 1170,232 1170,385 1030,462 890,385 890,232" fill="none" stroke="var(--line)" stroke-width="5" stroke-linejoin="round"/>
    <polygon points="670,418 820,500 820,665 670,748 520,665 520,500" fill="none" stroke="var(--line)" stroke-width="5" stroke-linejoin="round"/>
    <polygon points="870,136 1132,282 1132,574 870,721 608,574 608,282" fill="var(--ring)" stroke="var(--ring)" stroke-width="22" stroke-linejoin="round"/>
    <polygon points="870,166 1108,298 1108,562 870,694 632,562 632,298" fill="#e9eaec" stroke="#e9eaec" stroke-width="14" stroke-linejoin="round"/>
    <g role="img" aria-label="Foto: Steuerberater mit Brille prüft Unterlagen und Smartphone am Schreibtisch">
      <rect x="640" y="180" width="460" height="500" fill="url(#photo-tone)" clip-path="url(#photo-clip)"/>
    </g>
    <polygon points="675,158 728,188 728,248 675,278 622,248 622,188" fill="var(--navy-bright)" stroke="var(--navy-bright)" stroke-width="10" stroke-linejoin="round"/>
    <polygon points="675,175 713,197 713,240 675,262 637,240 637,197" fill="none" stroke="#fff" stroke-width="2" stroke-linejoin="round"/>
    <polygon points="1100,516 1142,540 1142,588 1100,612 1058,588 1058,540" fill="#fff" stroke="#fff" stroke-width="10" stroke-linejoin="round"/>
  </svg>

  <header class="site-header">
    <div class="brand"><span class="brand-square"></span>LM STEUERBERATUNG</div>
    <nav class="main-nav">
      <a class="active" href="#">HOME</a>
      <a class="has-sub" href="#">LEISTUNGEN
        <svg width="11" height="7" viewBox="0 0 11 7"><polygon points="0,0 11,0 5.5,7" fill="#1e1e1e"/></svg>
      </a>
      <a href="#">ÜBER MICH</a>
      <a href="#">KONTAKT</a>
      <a href="#">IMPRESSUM</a>
      <span class="lang">
        <svg width="24" height="24" viewBox="0 0 24 24">
          <clipPath id="flag-clip"><circle cx="12" cy="12" r="11.5"/></clipPath>
          <g clip-path="url(#flag-clip)">
            <rect width="24" height="8" fill="#111"/>
            <rect y="8" width="24" height="8" fill="#dd1c1c"/>
            <rect y="16" width="24" height="8" fill="#ffcc00"/>
          </g>
        </svg>
        GR
        <svg width="11" height="7" viewBox="0 0 11 7"><polyline points="1,1 5.5,5.5 10,1" fill="none" stroke="#1e1e1e" stroke-width="1.4"/></svg>
      </span>
    </nav>
  </header>

  <section class="hero-text">
    <p class="hero-kicker">WILLKOMMEN BEI</p>
    <h1 class="hero-title">LM-STEUERBERATUNG</h1>
    <p class="hero-lead">Ihrem Spezialisten bei allen steuerlichen Themen rund um Einkünfte &amp; Vermögen aus Krypto-Assets</p>
    <p class="hero-body">Dann mach ich eine Schweizer Holding-Gesellschaft– dort zahlt man fast keine Steuern</p>
    <a class="btn-primary" href="#">WEITER ZU UNSEREN LEISTUNGEN</a>
  </section>

  <div class="slider-controls">
    <span class="slider-btn" aria-label="Zurück">
      <svg width="14" height="24" viewBox="0 0 14 24"><polyline points="12,2 2,12 12,22" fill="none" stroke="#1e1e1e" stroke-width="2.2"/></svg>
    </span>
    <span class="slider-btn" aria-label="Weiter">
      <svg width="14" height="24" viewBox="0 0 14 24"><polyline points="2,2 12,12 2,22" fill="none" stroke="#1e1e1e" stroke-width="2.2"/></svg>
    </span>
  </div>
</div>
</body>
</html>
```